Telecommunications/Power civil contractor needs business card design

Were a new telecommunications/power underground civil contractor that is looking for a new business card design. Our company colours are silver or grey and orange. Feel free to use the white background logo or the black background logo.

Target Market(s)

Local contractors, utility companies, private sector mining/energy companies, developers.

Industry/Entity Type

Telecommunications

Contact Information for Business Card

Each card will need the following info:
Persons name:
Title:
E-mail:
Phone number:
Shop Address:
Mailing Address:

Requirements
Must have
• Each card will need the following info:
• Persons name:
• Title:
• E-mail:
• Phone number:
• Shop Address:
• Mailing Address:

```html
<!DOCTYPE html>
<html lang="en">
<head>
<meta charset="utf-8">
<title>Ridgeline Contracting Inc – Business Card</title>
<link rel="stylesheet" href="https://fonts.googleapis.com/css2?family=Open+Sans:wght@400;600;700&display=swap">
<style>
  :root {
    --backdrop: #2a2a2a;
    --card-white: #ffffff;
    --card-black: #050505;
    --brand-orange: #f15a24;
    --brand-grey: #58595b;
    --text-dark: #3a3a3a;
    --text-light: #ffffff;
  }
  * { box-sizing: border-box; margin: 0; padding: 0; }
  html, body {
    width: 1200px; height: 716px; overflow: hidden;
    background: var(--backdrop);
    font-family: "Open Sans", Arial, sans-serif;
  }
  .stage { position: relative; width: 1200px; height: 716px; }

  .card {
    position: absolute; top: 208px;
    width: 520px; height: 300px;
    border-radius: 4px; overflow: hidden;
    box-shadow: 0 8px 24px rgba(0,0,0,.45);
  }
  .card--front { left: 50px; background: var(--card-white); }
  .card--back  { left: 630px; background: var(--card-black); }

  .card__bands { position: absolute; inset: 0; }

  .brand {
    position: absolute; display: flex; flex-direction: column; align-items: center;
  }
  .brand__dot {
    width: 46px; height: 46px; border-radius: 50%;
    background: var(--brand-orange); margin-bottom: 6px;
  }
  .brand__name {
    font-weight: 700; color: var(--brand-orange);
    text-transform: uppercase; text-align: center; line-height: 1.1;
    letter-spacing: .5px;
  }
  .card--front .brand { left: 250px; top: 22px; width: 200px; }
  .card--front .brand__name { font-size: 17px; }
  .card--back .brand { right: 30px; bottom: 34px; width: 200px; }
  .card--back .brand__name { font-size: 17px; }

  .person {
    position: absolute; left: 0; top: 140px; width: 270px;
    text-align: center; color: var(--text-light);
  }
  .person__name { font-size: 14px; font-weight: 700; }
  .person__title { font-size: 13px; font-weight: 400; margin-top: 2px; }

  .contact {
    position: absolute; left: 290px; top: 180px;
    color: var(--text-light); font-size: 12.5px; list-style: none;
  }
  .contact__item { display: flex; align-items: center; gap: 8px; margin-bottom: 6px; }
  .contact__icon { width: 12px; height: 12px; fill: var(--brand-orange); flex: none; }

  .address {
    position: absolute; left: 0; width: 260px; top: 256px;
    text-align: center; font-size: 12.5px; color: var(--text-dark);
  }
</style>
</head>
<body>
<main class="stage">

  <section class="card card--front" aria-label="Business card front">
    <svg class="card__bands" width="520" height="300" viewBox="0 0 520 300" aria-hidden="true">
      <polygon fill="var(--brand-grey)" points="262,168 520,168 520,240 262,240"/>
      <polygon fill="var(--brand-orange)" points="0,128 100,128 108,136 116,128 280,128 280,188 262,206 0,206"/>
    </svg>

    <div class="brand">
      <span class="brand__dot"></span>
      <span class="brand__name">Ridgeline<br>Contracting Inc</span>
    </div>

    <div class="person">
      <p class="person__name">Morgan Hale</p>
      <p class="person__title">Managing Director</p>
    </div>

    <ul class="contact">
      <li class="contact__item">
        <svg class="contact__icon" viewBox="0 0 24 24" aria-hidden="true"><path d="M6.6 10.8a15.5 15.5 0 0 0 6.6 6.6l2.2-2.2a1 1 0 0 1 1-.25 11.4 11.4 0 0 0 3.6.57 1 1 0 0 1 1 1V20a1 1 0 0 1-1 1A17 17 0 0 1 3 4a1 1 0 0 1 1-1h3.5a1 1 0 0 1 1 1c0 1.25.2 2.45.57 3.57a1 1 0 0 1-.25 1z"/></svg>
        <span>555.010.2468</span>
      </li>
      <li class="contact__item">
        <svg class="contact__icon" viewBox="0 0 24 24" aria-hidden="true"><path d="M2 5h20v14H2z M4 7v.4l8 5 8-5V7z" fill-rule="evenodd"/></svg>
        <span>info@ridgelinecontracting.com</span>
      </li>
    </ul>

    <p class="address">12 Cedar Row, Suite 200, Alder Falls, WA 55501</p>
  </section>

  <section class="card card--back" aria-label="Business card back">
    <div class="brand">
      <span class="brand__dot"></span>
      <span class="brand__name">Ridgeline<br>Contracting Inc</span>
    </div>
  </section>

</main>
</body>
</html>
```